I need a business card design for my vidloomer channel called The Tidy Skillet Show. I make vidloomer cooking tutorials. I'd like the phrase " I'll see you next time, for my next meal" somewhere on the BC. The Vidloomer web address is www.vidloomer.example/user/TidySkilletShow
email - bookings@harrowlanemedia.example

Target Market(s)

This is for companies & business opportunities so it needs to look professional & sleek.

Industry/Entity Type

Cooking

Requirements
Must have
• Must have my Tidy skillet show logo on the card preferably top left. My name ( Marcus Delroy ). Name of my channel "Tidy Skillet Show" & the vidlomer logo & web address for my channel & the email bookings@harrowlanemedia.example & the 3 pics of food.

```html
<!DOCTYPE html>
<html lang="en">
<head>
<meta charset="utf-8">
<title>Tidy Skillet Show – Business Card</title>
<link rel="stylesheet" href="https://fonts.googleapis.com/css2?family=Fredoka:wght@600&family=Josefin+Sans:wght@400;600&family=Roboto:wght@400&display=swap">
<style>
  :root {
    --canvas: #ecebe8;
    --ink: #111111;
    --orange: #f7a11d;
    --white: #ffffff;
    --text-dark: #2b2b2b;
    --red: #d8262b;
    --navy: #23358f;
    --pool-light: #ece7a8;
    --pool-deep: #d9d27e;
    --cake-top: #8a4a2c;
    --cake-bottom: #c9473f;
    --slice-top: #c8322e;
    --slice-bottom: #3f64ad;
  }
  * { box-sizing: border-box; margin: 0; padding: 0; }
  html, body { width: 1200px; height: 1000px; overflow: hidden; }
  body { background: var(--canvas); position: relative; }

  .card {
    position: absolute; left: 100px; top: 214px;
    width: 1000px; height: 572px;
    background: var(--white); overflow: hidden;
    box-shadow: 0 6px 20px rgba(0,0,0,.18);
  }
  .header-band {
    position: absolute; left: 0; top: 0; width: 1000px; height: 262px;
    background: var(--ink);
  }
  .tagline-panel {
    position: absolute; left: 650px; top: 0; width: 350px; height: 310px;
  }
  .tagline-panel svg { position: absolute; inset: 0; }
  .tagline {
    position: absolute; left: 100px; top: 36px; width: 240px;
    font-family: "Josefin Sans", sans-serif; font-weight: 400;
    font-size: 30px; line-height: 40px; text-align: center;
    color: var(--text-dark); text-transform: uppercase;
  }

  .brand-mark {
    position: absolute; left: 34px; top: 36px; width: 220px; height: 200px;
    display: flex; flex-direction: column; align-items: center; justify-content: center; gap: 16px;
  }
  .brand-mark .dot {
    width: 70px; height: 70px; border-radius: 50%; background: var(--orange);
  }
  .brand-mark .brand-name {
    font-family: "Fredoka", sans-serif; font-weight: 600;
    font-size: 24px; line-height: 28px; text-align: center; color: var(--orange);
  }

  .channel-title {
    position: absolute; left: 270px; top: 34px; width: 400px;
    text-align: center; font-family: "Fredoka", sans-serif; font-weight: 600;
    color: var(--orange); text-transform: uppercase;
  }
  .channel-title .line { display: block; font-size: 64px; line-height: 66px; }
  .channel-title .sub {
    display: block; margin-top: 4px;
    font-family: "Josefin Sans", sans-serif; font-weight: 600;
    font-size: 34px; line-height: 40px; letter-spacing: 2px; color: var(--white);
  }

  .host-name {
    position: absolute; left: 32px; top: 292px;
    font-family: "Fredoka", sans-serif; font-weight: 600;
    font-size: 56px; line-height: 66px; color: var(--orange); text-transform: uppercase;
  }
  .contact { position: absolute; left: 32px; display: flex; align-items: center; gap: 24px; }
  .contact.web { top: 390px; }
  .contact.mail { top: 476px; }
  .contact .icon { width: 58px; height: 38px; flex: none; }
  .contact .text {
    font-family: "Roboto", sans-serif; font-size: 22px; line-height: 28px; color: var(--text-dark);
  }

  .food { position: absolute; }
  .food.pool-cake {
    left: 500px; top: 286px; width: 200px; height: 236px; border-radius: 14px;
    background: linear-gradient(160deg, var(--pool-light), var(--pool-deep));
  }
  .food.candy-cake {
    left: 690px; top: 230px; width: 310px; height: 320px; border-radius: 110px 0 0 0;
    background: linear-gradient(180deg, var(--cake-top), var(--cake-bottom));
  }
  .food.jelly-slice {
    left: 590px; top: 448px; width: 170px; height: 102px; border-radius: 8px;
    background: linear-gradient(180deg, var(--slice-top), var(--slice-bottom));
  }

  .footer-band {
    position: absolute; left: 0; bottom: 0; width: 1000px; height: 22px; background: var(--orange);
  }
</style>
</head>
<body>
  <main class="card">
    <div class="header-band"></div>

    <div class="brand-mark">
      <span class="dot"></span>
      <span class="brand-name">The Tidy Skillet Show</span>
    </div>

    <h1 class="channel-title">
      <span class="line">Tidy</span>
      <span class="line">Skillet</span>
      <span class="sub">Show</span>
    </h1>

    <div class="tagline-panel">
      <svg width="350" height="310" viewBox="0 0 350 310" aria-hidden="true">
        <path d="M90 0 H350 V310 H90 Q30 240 30 155 Q30 60 90 0 Z" fill="#ffffff"/>
        <path d="M104 0 H350 V310 H104 Q46 240 46 155 Q46 60 104 0 Z" fill="#f7a11d"/>
      </svg>
      <p class="tagline">I'll see you next time, for my next meal</p>
    </div>

    <h2 class="host-name">Marcus Delroy</h2>

    <div class="contact web">
      <svg class="icon" viewBox="0 0 58 38" aria-hidden="true"><circle cx="29" cy="19" r="17" fill="#d8262b"/></svg>
      <span class="text">www.vidloomer.example/user/<br>TidySkilletShow</span>
    </div>

    <div class="contact mail">
      <svg class="icon" viewBox="0 0 58 38" aria-hidden="true">
        <rect x="2" y="2" width="54" height="34" rx="4" fill="#23358f"/>
        <path d="M6 7 L29 23 L52 7" fill="none" stroke="#ffffff" stroke-width="3"/>
      </svg>
      <span class="text">bookings@harrowlanemedia.example</span>
    </div>

    <div class="food pool-cake" role="img" aria-label="Photo of a yellow frosted sheet cake decorated as a pool party"></div>
    <div class="food candy-cake" role="img" aria-label="Photo of a chocolate-frosted layer cake covered in colourful candies, cut open to show a candy-filled centre"></div>
    <div class="food jelly-slice" role="img" aria-label="Photo of a slice of rainbow layered jelly cake"></div>

    <div class="footer-band"></div>
  </main>
</body>
</html>
```